Business card design for a dynamic IT consulting company

We need a business card design for a young firm, specialized in the Telecommunications/Consulting industry. The name of the company is Quindor and Partners Business Consulting Ltd. (Short name: Quindor and Partnes)
Quindor = solve read reverse, so we aim to be uncomplicated and solution-oriented. The small pipe in our logo is also related to the word solve. So we need a new business card design, which is simple, eye catching and something non traditional (I would probably prefer a square shaped design rather than a rectangle, but open for suggestions). Attached our logo.

Target Market(s)

Usually our customers are Tier1 Telecoms providers (Q-Netra, Palorix, etc) and their executives.

Industry/Entity Type

Business

Contact Information for Business Card

Name: Bence Tolnavari
Email: b.tolnavari@quindor.hu
Web: www.quindor.hu
Mobile: +36 30 518 2769
Title: Managing Director

Optional:
Company name: Quindor and Partners Ltd.
Address: 1087 Budapest, Tolvenka str. 28/C, Hungary

Font styles to use
Other font styles liked:
• helveticaneue_medium, Prime Regular are used now.

Colors

Designer to choose colors to be used in the design.

Requirements
Must have
• I would like to have a 2 sided design.
Nice to have
• I thought if we make the logo a bit bigger (without the company name), that could go to the back with the company name below. I though, if the pipe in the logo is somehow touchable on the business card, would be nice and unique.

```html
<!DOCTYPE html>
<html lang="en">
<head>
<meta charset="utf-8">
<title>Quindor and Partners – Business Card</title>
<link href="https://fonts.googleapis.com/css2?family=Exo+2:wght@500;600&family=Roboto:wght@400&display=swap" rel="stylesheet">
<style>
  :root {
    --backdrop: #3b332e;
    --card: #141414;
    --card-edge: #1d1d1d;
    --emboss: #5b5b5b;
    --white: #f4f4f4;
    --magenta: #b5319b;
    --cyan: #139bd8;
  }
  html, body {
    margin: 0;
    padding: 0;
    width: 1200px;
    height: 780px;
    overflow: hidden;
    background: var(--backdrop);
  }
  .canvas {
    position: relative;
    width: 1200px;
    height: 780px;
  }
  .card {
    position: absolute;
    top: 240px;
    width: 520px;
    height: 300px;
    border-radius: 22px;
    background: radial-gradient(ellipse at 40% 30%, var(--card-edge), var(--card) 70%);
    overflow: hidden;
    box-shadow: 0 14px 30px rgba(0,0,0,0.45);
  }
  .card--back { left: 50px; }
  .card--front { left: 630px; }

  .company-name {
    font-family: "Exo 2", sans-serif;
    font-weight: 500;
    line-height: 1;
    margin: 0;
    white-space: nowrap;
  }

  /* Back side: company name */
  .back-content {
    position: absolute;
    inset: 0;
    display: flex;
    align-items: center;
    justify-content: center;
  }
  .back-content .company-name {
    font-size: 34px;
    color: var(--emboss);
  }

  /* Front side: contact details */
  .front-content {
    position: absolute;
    left: 38px;
    top: 104px;
  }
  .front-content .company-name {
    font-size: 26px;
    color: var(--white);
  }
  .person-name {
    font-family: "Exo 2", sans-serif;
    font-weight: 600;
    font-size: 18px;
    line-height: 1.2;
    color: var(--white);
    margin: 18px 0 0;
  }
  .person-title {
    font-family: "Roboto", sans-serif;
    font-size: 13px;
    color: var(--magenta);
    margin: 2px 0 10px;
  }
  .contact-list {
    list-style: none;
    margin: 0;
    padding: 0;
    font-family: "Roboto", sans-serif;
    font-size: 13px;
    color: var(--white);
  }
  .contact-list li {
    display: flex;
    align-items: center;
    gap: 8px;
    height: 19px;
  }
  .contact-icon { width: 11px; height: 11px; flex: none; }

  /* Right edge colour band */
  .edge-rule {
    position: absolute;
    top: 0;
    bottom: 0;
    left: 462px;
    width: 4px;
    background: var(--white);
  }
  .edge-band {
    position: absolute;
    top: 0;
    bottom: 0;
    left: 472px;
    right: 0;
    display: flex;
    flex-direction: column;
  }
  .edge-band__magenta { flex: 1; background: var(--magenta); }
  .edge-band__cyan { flex: 1.1; background: var(--cyan); }
</style>
</head>
<body>
<main class="canvas">

  <section class="card card--back" aria-label="Card back">
    <div class="back-content">
      <p class="company-name">Quindor and Partners</p>
    </div>
  </section>

  <section class="card card--front" aria-label="Card front">
    <div class="front-content">
      <p class="company-name">Quindor and Partners</p>
      <p class="person-name">Bence Tolnavari</p>
      <p class="person-title">Managing Director</p>
      <ul class="contact-list">
        <li>
          <svg class="contact-icon" viewBox="0 0 11 11" aria-hidden="true"><rect x="1.5" y="0.75" width="8" height="9.5" rx="1" fill="none" stroke="var(--magenta)" stroke-width="1.4"/></svg>
          +36 30 518 2769
        </li>
        <li>
          <svg class="contact-icon" viewBox="0 0 11 11" aria-hidden="true"><rect x="0.5" y="2" width="10" height="7" fill="var(--white)"/><path d="M0.5 2 L5.5 6 L10.5 2" fill="none" stroke="var(--card)" stroke-width="1"/></svg>
          b.tolnavari@quindor.hu
        </li>
        <li>
          <svg class="contact-icon" viewBox="0 0 11 11" aria-hidden="true"><circle cx="5.5" cy="5.5" r="5" fill="var(--cyan)"/><path d="M0.5 5.5 H10.5 M5.5 0.5 V10.5" stroke="var(--card)" stroke-width="0.7"/><ellipse cx="5.5" cy="5.5" rx="2.2" ry="5" fill="none" stroke="var(--card)" stroke-width="0.7"/></svg>
          www.quindor.hu
        </li>
      </ul>
    </div>
    <div class="edge-rule"></div>
    <div class="edge-band">
      <div class="edge-band__magenta"></div>
      <div class="edge-band__cyan"></div>
    </div>
  </section>

</main>
</body>
</html>
```